NZ First of it's kind solutions directory and marketplace for busy Mums needs a business card design

We need a business card design for our new nationwide business in NZ (long term plans to go global). We provide solutions to the everyday challenges that busy Mums face by connecting them with quality communities and suppliers of carefully selected, relevant products and services. We sell direct via our online marketplace. The final design should communicate our values of inclusivity, quality and smart solutions. Colours should incorporate our logo colour palette of #477077 and #6ba8b2. Our website is at https://www.brightnestmums.example

Target Market(s)

busy Mums, Age 28 – 50, female, income over $100K, location main centres NZ primarily but NZ wide. Is likely juggling work or career with a young family. Probably had hobbies which have fallen by the wayside.
-Wants to succeed in her chosen career without compromising on family life
-to successfully juggle her career without feeling like she is compromising her children
- Is time poor, something always has to give and it’s generally her health (she’ll stay up late, get stressed)
- probably ex corporate or professional career. Has discretional income

Industry/Entity Type

Business

Contact Information for Business Card

Lena Forbisher, Founder, BrightNestMums.example (Strapline Tap; Gather; Sorted), 47 Kowhai Terrace, Ellerslie, Auckland 1051, New Zealand. Mob: 021 483 517 Ph: +64 (0)9 571 4860

Font styles to use
Other font styles liked:
• Raleway, and/or Architects Daughter

Colors
00a990
33b8a4
86cfc6
cfeae6

Requirements
Must have
• the above details, streamline. the logo and colours associated with those logos
Should not have
• foil or metallic colours

```html
<!DOCTYPE html>
<html lang="en">
<head>
<meta charset="utf-8">
<title>BrightNestMums business card</title>
<link href="https://fonts.googleapis.com/css2?family=Roboto:ital,wght@0,400;0,500;0,700;1,400&display=swap" rel="stylesheet">
<style>
  :root {
    --backdrop: #e4e4e4;
    --card: #f7f7f7;
    --brand-dark: #477077;
    --brand-light: #6ba8b2;
    --mark-fill: #3c5e66;
    --ink: #3a3f42;
    --accent-dot: #79bde3;
  }
  * { margin: 0; padding: 0; box-sizing: border-box; }
  html, body {
    width: 1200px; height: 576px; overflow: hidden;
    background: var(--backdrop);
    font-family: "Roboto", Arial, sans-serif;
    color: var(--ink);
  }
  .canvas { position: relative; width: 1200px; height: 576px; }
  .card {
    position: absolute; top: 138px;
    width: 484px; height: 294px;
    background: var(--card);
    border-radius: 14px;
    overflow: hidden;
  }
  .card--front { left: 82px; }
  .card--back { left: 602px; }

  .brand-circle {
    position: absolute;
    border-radius: 50%;
    background: var(--mark-fill);
  }
  .card--front .brand-circle { left: 14px; top: 110px; width: 176px; height: 176px; }
  .card--back .brand-circle { left: 280px; top: 100px; width: 196px; height: 196px; }

  .wordmark {
    font-family: "Roboto", Arial, sans-serif;
    font-weight: 700;
    color: var(--brand-dark);
    letter-spacing: -0.5px;
    line-height: 1;
    white-space: nowrap;
  }
  .strapline {
    font-size: 11.5px;
    letter-spacing: 4px;
    color: var(--ink);
    white-space: nowrap;
    margin-top: 9px;
  }
  .strapline .divider { color: var(--brand-light); margin: 0 5px; }

  .card--front .brand-lockup { position: absolute; left: 212px; top: 200px; }
  .card--front .wordmark { font-size: 31px; }

  .card--back .brand-lockup { position: absolute; left: 26px; top: 30px; }
  .card--back .wordmark { font-size: 31px; }

  .edge-dot {
    position: absolute; left: -10px; top: 109px;
    width: 20px; height: 20px; border-radius: 50%;
    background: var(--accent-dot);
  }

  .person { position: absolute; left: 26px; top: 106px; }
  .person__name { font-size: 20px; font-weight: 500; color: var(--brand-dark); }
  .person__role { font-size: 12px; font-style: italic; margin-top: 3px; }

  .address { position: absolute; left: 26px; top: 164px; font-size: 12.5px; line-height: 18px; }

  .contact-list { position: absolute; left: 26px; top: 213px; list-style: none; font-size: 12.5px; }
  .contact-list li { display: flex; align-items: center; height: 18.5px; }
  .contact-list svg { width: 11px; height: 11px; margin-right: 8px; fill: var(--brand-light); }
</style>
</head>
<body>
<main class="canvas">

  <section class="card card--front" aria-label="Business card front">
    <div class="brand-circle"></div>
    <div class="brand-lockup">
      <div class="wordmark">BrightNestMums</div>
      <div class="strapline">TAP<span class="divider">|</span>GATHER<span class="divider">|</span>SORTED</div>
    </div>
  </section>

  <section class="card card--back" aria-label="Business card back">
    <div class="brand-lockup">
      <div class="wordmark">BrightNestMums</div>
      <div class="strapline">TAP<span class="divider">|</span>GATHER<span class="divider">|</span>SORTED</div>
    </div>
    <div class="edge-dot"></div>
    <div class="brand-circle"></div>

    <div class="person">
      <div class="person__name">Lena Forbisher</div>
      <div class="person__role">Founder</div>
    </div>

    <address class="address" style="font-style:normal">
      47 Kowhai Terrace, Ellerslie,<br>Auckland 1051, New Zealand
    </address>

    <ul class="contact-list">
      <li><svg viewBox="0 0 12 12" aria-hidden="true"><rect x="3" y="0.5" width="6" height="11" rx="1.2"/><rect x="4" y="2" width="4" height="6.5" fill="#f7f7f7"/></svg>021 483 517</li>
      <li><svg viewBox="0 0 12 12" aria-hidden="true"><path d="M1 4c0-2 2-3 5-3s5 1 5 3v1H8.5V3.8h-5V5H1z"/><rect x="2" y="6" width="8" height="5" rx="1"/></svg>+64 (0)9 571 4860</li>
      <li><svg viewBox="0 0 12 12" aria-hidden="true"><circle cx="6" cy="6" r="5.2"/><path d="M1 6h10M6 1c-2 2-2 8 0 10M6 1c2 2 2 8 0 10" stroke="#f7f7f7" stroke-width="0.9" fill="none"/></svg>www.BrightNestMums.example</li>
      <li><svg viewBox="0 0 12 12" aria-hidden="true"><rect x="0.5" y="2.5" width="11" height="7.5"/><path d="M0.8 2.8L6 7l5.2-4.2" stroke="#f7f7f7" stroke-width="0.9" fill="none"/></svg>lenaforbisher@brightnestmums.example</li>
    </ul>
  </section>

</main>
</body>
</html>
```